Nutrition business needs logo & business card design

We need a business card & logo design for a new company based in Toronto, Ontario Canada called Verdel Wellworks.

We provide nutrition service using metrics as guide to manage client's progress. Our service creates individualized nutrition and lifestyle strategies that focuses on improving Performance, Longevity and Weight Loss. I would like to see designs that use the color of green, gray, blue and white.

The final design should:

--convey a feeling of connectedness with positive transformation.

-- communicate the idea of awareness with guided effort that yields personal independence for a better and more productive life

Target Market(s)

Professionals who work in the IT/Computer/Engineering/Banking industry specifically Directors, Managers, CEO's.

Industry/Entity Type

Health And Wellness

Contact Information for Business Card

Dorvane Pike, Owner
email: DPIKE@verdelwellworks.example
tel: - 555-204-7718

Logo Text

better health through analytics or measure to manage

Font styles to use
Other font styles liked:
• Garamound

Colors
ffffff
abd037
85acd3
757575
34a7d7

Requirements
Must have
• Good contrast and decent size font - ease of readability, aesthetically nice colors
Nice to have
• image of chart or graph that conveys measurement or analytics
Should not have
• Borders, images of food,

```html
<!DOCTYPE html>
<html lang="en">
<head>
<meta charset="utf-8">
<title>Verdel Wellworks — Business Card</title>
<link href="https://fonts.googleapis.com/css2?family=Raleway:wght@300;400&family=Poppins:wght@600&family=Dancing+Script:wght@500&display=swap" rel="stylesheet">
<style>
  :root {
    --backdrop: #e8e5df;
    --card: #ffffff;
    --grid: rgba(133, 172, 211, 0.16);
    --chart-line: rgba(117, 117, 117, 0.22);
    --brand-green: #abd037;
    --ink: #333333;
    --ink-soft: #555555;
  }
  * { box-sizing: border-box; margin: 0; padding: 0; }
  html, body {
    width: 1200px;
    height: 1023px;
    overflow: hidden;
    background: var(--backdrop);
  }
  .stage {
    width: 1200px;
    height: 1023px;
    display: flex;
    align-items: center;
    justify-content: center;
  }
  .business-card {
    position: relative;
    width: 840px;
    height: 480px;
    background-color: var(--card);
    background-image:
      linear-gradient(var(--grid) 1px, transparent 1px),
      linear-gradient(90deg, var(--grid) 1px, transparent 1px);
    background-size: 22px 22px;
    box-shadow: 0 10px 30px rgba(0, 0, 0, 0.18);
    overflow: hidden;
  }
  .analytics-trace {
    position: absolute;
    inset: 0;
    width: 100%;
    height: 100%;
  }
  .brand-block {
    position: absolute;
    left: 90px;
    top: 112px;
    display: flex;
    align-items: center;
    gap: 26px;
  }
  .brand-dot {
    width: 84px;
    height: 84px;
    border-radius: 50%;
    background: var(--brand-green);
    flex-shrink: 0;
  }
  .brand-name {
    font-family: "Raleway", sans-serif;
    font-weight: 400;
    font-size: 26px;
    letter-spacing: 0.5em;
    color: var(--ink);
    white-space: nowrap;
  }
  .tagline {
    position: absolute;
    left: 200px;
    top: 188px;
    font-family: "Dancing Script", cursive;
    font-size: 20px;
    color: var(--ink-soft);
    white-space: nowrap;
  }
  .contact-block {
    position: absolute;
    left: 200px;
    top: 258px;
    display: grid;
    grid-template-columns: auto auto;
    column-gap: 36px;
    row-gap: 6px;
    align-items: baseline;
  }
  .person-name {
    font-family: "Poppins", sans-serif;
    font-weight: 600;
    font-size: 30px;
    color: var(--ink);
    white-space: nowrap;
  }
  .person-role,
  .contact-line {
    font-family: "Raleway", sans-serif;
    font-weight: 300;
    font-size: 21px;
    color: var(--ink);
    white-space: nowrap;
  }
</style>
</head>
<body>
  <main class="stage">
    <section class="business-card" aria-label="Verdel Wellworks business card">
      <svg class="analytics-trace" viewBox="0 0 840 480" aria-hidden="true">
        <polyline points="0,150 90,130 150,175 210,60 240,0" fill="none" stroke="var(--chart-line)" stroke-width="1.5"/>
        <polyline points="560,0 600,120 640,175 700,300 760,360 840,420" fill="none" stroke="var(--chart-line)" stroke-width="1.5"/>
        <polyline points="380,480 430,420 500,440 560,380" fill="none" stroke="var(--chart-line)" stroke-width="1.5"/>
      </svg>

      <div class="brand-block">
        <span class="brand-dot" aria-hidden="true"></span>
        <span class="brand-name">VERDEL WELLWORKS</span>
      </div>
      <p class="tagline">Healthy Lifestyle, Healthy life</p>

      <div class="contact-block">
        <span class="person-name">Dorvane Pike</span>
        <span class="contact-line">DPIKE@verdelwellworks.example</span>
        <span class="person-role">Owner</span>
        <span class="contact-line">555-204-7718</span>
      </div>
    </section>
  </main>
</body>
</html>
```